Business Card Design (NEW FILES)

ATTENTION: New vector files are available. Please update your design to reflect/use the new (better resolution) logo images.

Seeking a unique and professional business card design for a commercial drone photography/videography business. The layout should feature
the logo (attached) and include the following information:
Owen Tarrick
614-502-7738
www.skylarkreelworks.example
NRD Certified Remote Pilot

Owen Tarrick

```html
<!DOCTYPE html>
<html lang="en">
<head>
<meta charset="utf-8">
<title>Skylark Reelworks — Business Card</title>
<link rel="stylesheet" href="https://fonts.googleapis.com/css2?family=Open+Sans:ital,wght@0,400;0,600;0,800;1,400&display=swap">
<style>
  :root {
    --stage: #232323;
    --navy: #161a47;
    --navy-pattern: #1d2566;
    --navy-pattern-light: #2a3890;
    --orange: #e8823a;
    --white: #ffffff;
  }
  * { box-sizing: border-box; margin: 0; padding: 0; }
  html, body {
    width: 1200px; height: 780px; overflow: hidden;
    background: var(--stage);
    font-family: "Open Sans", Arial, sans-serif;
  }
  .sheet {
    position: relative; width: 1200px; height: 780px;
    display: flex; align-items: center; justify-content: center; gap: 40px;
  }
  .card {
    position: relative; width: 540px; height: 310px;
    background: var(--navy); overflow: hidden;
    box-shadow: 0 10px 30px rgba(0,0,0,0.45);
  }

  /* Front */
  .brand {
    position: absolute; left: 0; top: 92px; width: 270px;
    text-align: center; color: var(--white);
    font-weight: 600; font-size: 21px; letter-spacing: 0.5px;
  }
  .brand-dot {
    display: inline-block; width: 12px; height: 12px; border-radius: 50%;
    background: var(--orange); margin-right: 8px; vertical-align: 1px;
  }
  .divider {
    position: absolute; left: 270px; top: 58px; width: 1.5px; height: 190px;
    background: var(--orange);
  }
  .credential {
    position: absolute; left: 0; bottom: 48px; width: 270px;
    text-align: center; color: var(--white);
    font-style: italic; font-size: 12.5px;
  }
  .identity { position: absolute; left: 300px; top: 96px; }
  .name { font-weight: 800; font-size: 25px; line-height: 1; color: var(--white); }
  .name-first { color: var(--orange); }
  .role { color: var(--white); font-size: 11.5px; margin-top: 4px; }
  .contacts { list-style: none; margin-top: 18px; }
  .contact {
    display: flex; align-items: center; gap: 8px;
    color: var(--white); font-size: 12.5px; line-height: 1.7;
  }
  .contact svg { width: 13px; height: 13px; flex: none; fill: var(--orange); }

  /* Back */
  .pattern-field {
    position: absolute; inset: 0;
    background: linear-gradient(135deg, var(--navy-pattern) 0%, var(--navy) 55%, var(--navy-pattern-light) 100%);
    opacity: 0.7;
  }
  .back-brand {
    position: absolute; right: 40px; bottom: 44px;
    color: var(--white); font-weight: 600; font-size: 11px; letter-spacing: 0.3px;
  }
</style>
</head>
<body>
<main class="sheet">
  <section class="card card-front">
    <div class="brand"><span class="brand-dot"></span>Skylark Reelworks</div>
    <div class="divider"></div>
    <p class="credential">NRD Certified Remote Pilot Fully Insured</p>
    <div class="identity">
      <h1 class="name"><span class="name-first">Owen</span> Tarrick</h1>
      <p class="role">Owner</p>
      <ul class="contacts">
        <li class="contact">
          <svg viewBox="0 0 24 24" aria-hidden="true"><path d="M6.6 10.8a15.1 15.1 0 0 0 6.6 6.6l2.2-2.2c.3-.3.7-.4 1-.2 1.1.4 2.3.6 3.6.6.6 0 1 .4 1 1V20c0 .6-.4 1-1 1A17 17 0 0 1 3 4c0-.6.4-1 1-1h3.5c.6 0 1 .4 1 1 0 1.3.2 2.5.6 3.6.1.3 0 .7-.2 1z"/></svg>
          614-502-7738
        </li>
        <li class="contact">
          <svg viewBox="0 0 24 24" aria-hidden="true"><path d="M12 2a10 10 0 1 0 0 20 10 10 0 0 0 0-20zm6.9 6h-2.9a15.6 15.6 0 0 0-1.4-3.6A8 8 0 0 1 18.9 8zM12 4c.8 1.2 1.5 2.5 1.9 4h-3.8c.4-1.5 1.1-2.8 1.9-4zM4.3 14a8 8 0 0 1 0-4h3.4a16 16 0 0 0 0 4zm.8 2h2.9c.3 1.3.8 2.5 1.4 3.6A8 8 0 0 1 5.1 16zM8 8H5.1a8 8 0 0 1 4.3-3.6C8.8 5.5 8.4 6.7 8 8zm4 12c-.8-1.2-1.5-2.5-1.9-4h3.8c-.4 1.5-1.1 2.8-1.9 4zm2.3-6H9.7a14.7 14.7 0 0 1 0-4h4.6a14.7 14.7 0 0 1 0 4zm.3 5.6c.6-1.1 1.1-2.3 1.4-3.6h2.9a8 8 0 0 1-4.3 3.6zm1.7-5.6a16 16 0 0 0 0-4h3.4a8 8 0 0 1 0 4z"/></svg>
          www.skylarkreelworks.example
        </li>
        <li class="contact">
          <svg viewBox="0 0 24 24" aria-hidden="true"><path d="M20 4H4a2 2 0 0 0-2 2v12a2 2 0 0 0 2 2h16a2 2 0 0 0 2-2V6a2 2 0 0 0-2-2zm0 4-8 5-8-5V6l8 5 8-5z"/></svg>
          info@skylarkreelworks.example
        </li>
      </ul>
    </div>
  </section>

  <section class="card card-back">
    <div class="pattern-field" role="img" aria-label="Repeating embossed drone silhouette pattern in deep blue tones"></div>
    <div class="back-brand">Skylark Reelworks</div>
  </section>
</main>
</body>
</html>
```